Marwick Law Letterhead

We need a new letterhead design for a Law Firm. The address for the law firm is 1475 Calloway Street, Suite 210, Houston, Texas 77041. Phone Number: 832-361-9027; Fax Number: 832-614-7359. The logo is uploaded to the project.

```html
<!DOCTYPE html>
<html lang="en">
<head>
<meta charset="utf-8">
<title>Marwick Law Letterhead</title>
<link href="https://fonts.googleapis.com/css2?family=Roboto:wght@400;500&display=swap" rel="stylesheet">
<style>
  :root {
    --backdrop: #dcdcdc;
    --paper: #f1f1f1;
    --navy: #1b2a55;
    --red: #c8202b;
    --ink: #2b2b2b;
    --signature-tone: #d6d6d6;
  }
  * { margin: 0; padding: 0; box-sizing: border-box; }
  html, body { width: 1069px; height: 1200px; overflow: hidden; }
  body {
    background: var(--backdrop);
    font-family: "Roboto", Arial, sans-serif;
    color: var(--ink);
    position: relative;
  }
  .letterhead {
    position: absolute;
    left: 124px;
    top: 20px;
    width: 821px;
    height: 1160px;
    background: var(--paper);
    box-shadow: 0 4px 18px rgba(0,0,0,0.18);
  }
  .brand {
    position: absolute;
    left: 47px;
    top: 82px;
    display: flex;
    align-items: center;
    gap: 14px;
  }
  .brand-square {
    width: 56px;
    height: 56px;
    background: var(--navy);
  }
  .brand-name {
    font-size: 38px;
    font-weight: 500;
    color: var(--navy);
    letter-spacing: 0.5px;
  }
  .letter-body {
    position: absolute;
    left: 47px;
    top: 328px;
    width: 728px;
    font-size: 15px;
    line-height: 23.6px;
  }
  .recipient { margin-bottom: 17px; }
  .letter-body p.paragraph {
    text-align: justify;
    margin-bottom: 16px;
  }
  .letter-body p.paragraph.spaced { margin-bottom: 26px; }
  .closing { margin-top: 18px; }
  .signature {
    display: block;
    margin-top: 14px;
    width: 146px;
    height: 58px;
    background: var(--signature-tone);
    border-radius: 4px;
  }
  .footer-rule {
    position: absolute;
    left: 0;
    right: 0;
    top: 1079px;
    height: 1.5px;
    background: var(--navy);
  }
  .contact-bar {
    position: absolute;
    left: 52px;
    top: 1108px;
    display: flex;
    align-items: center;
    gap: 14px;
    font-size: 16px;
    color: var(--ink);
  }
  .contact-item { display: flex; align-items: center; gap: 5px; }
  .contact-item svg { fill: var(--red); }
</style>
</head>
<body>
  <div class="letterhead">
    <div class="brand">
      <div class="brand-square"></div>
      <div class="brand-name">Marwick Law</div>
    </div>

    <div class="letter-body">
      <div class="recipient">
        Mr/s<br>
        First Name and Last Name<br>
        Company Name<br>
        Address
      </div>
      <p class="paragraph spaced">Lorem Ipsum is simply dummy text of the printing and typesetting industry. Lorem Ipsum has been the industry's standard dummy text ever since the 1500s, when an unknown printer took a galley of type and scrambled it to make a type specimen book. It has survived not only five centuries, but also the leap into electronic typesetting, remaining essentially unchanged. It was popularised in the 1960s with the release of Typeset sheets containing Lorem Ipsum passages.</p>
      <p class="paragraph">he standard chunk of Lorem Ipsum used since the 1500s is reproduced below for those interested. Sections 1.10.32 and 1.10.33 from "de Finibus Bonorum et Malorum" by Corvinus are also reproduced in their exact original form, accompanied by English versions from the 1914 translation by H. Ashdown. Lorem ipsum dolor sit amet, consectetur adipiscing elit, sed do eiusmod tempor incididunt ut labore et dolore magna aliqua.</p>
      <p class="paragraph">It is a long established fact that a reader will be distracted by the readable content of a page when looking at its layout. The point of using Lorem Ipsum is that it has a more-or-less normal distribution of letters, as opposed to using 'Content here, content here', making it look like readable English. Many desktop publishing packages and web page editors now .</p>
      <div class="closing">Your Sincerely,</div>
      <span class="signature" role="img" aria-label="Handwritten signature of the sender"></span>
    </div>

    <div class="footer-rule"></div>
    <div class="contact-bar">
      <span class="contact-item">
        <svg width="13" height="13" viewBox="0 0 24 24" aria-hidden="true"><path d="M6.6 10.8a15.1 15.1 0 0 0 6.6 6.6l2.2-2.2c.3-.3.7-.4 1-.2 1.1.4 2.3.6 3.6.6.6 0 1 .4 1 1V20c0 .6-.4 1-1 1A17 17 0 0 1 3 4c0-.6.4-1 1-1h3.5c.6 0 1 .4 1 1 0 1.3.2 2.5.6 3.6.1.3 0 .7-.2 1z"/></svg>
        832-361-9027
      </span>
      <span class="contact-item">
        <svg width="13" height="13" viewBox="0 0 24 24" aria-hidden="true"><path d="M6 2h12v5H6zM4 8h16a2 2 0 0 1 2 2v7h-4v5H6v-5H2v-7a2 2 0 0 1 2-2zm4 8v4h8v-4z"/></svg>
        832-614-7359
      </span>
      <span class="contact-item">
        <svg width="12" height="15" viewBox="0 0 24 30" aria-hidden="true"><path d="M12 0a10 10 0 0 0-10 10c0 7.5 10 20 10 20s10-12.5 10-20A10 10 0 0 0 12 0zm0 14a4 4 0 1 1 0-8 4 4 0 0 1 0 8z"/></svg>
        1475 Calloway Street, Suite 210, Houston, Texas 77041
      </span>
    </div>
  </div>
</body>
</html>
```